Car wash line needed for the pylon inscription

We need a design template / print template for our advertising pylon so that the Korvane plates can be printed. The area to be printed is approx. 1.5m wide and approx. 2.70m high. We operate a car wash about 30m long. The washing rollers are equipped with scratch-free Velmo Tex foam material. Before the vehicle is put into the car wash it gets a manual high pressure pre-wash. There are four different washing programs: basic laundry € 7.50 (wheel cleaning, intensive washing, gloss drying comfort care € 10.50 (like base + active foam) special care € 13.00 (like comfort + glossy sealing with lotus wax) premium care € 15.50 (like special care + Underbody wash) The pylon is right on the driveway on a busy road, we want to achieve maximum attention with the pylons. It should not be too much content because the vehicles drive past it, due to an immediate gyro, the speed is however at about 40Km / h. Opening hours Mon-Fri. 08: 00-19: 00 Sat 07: 00-19: 00 The Korvane plates are red. The enclosed files show our pylon with a little appealing design proposal our advertising agency and the real local places. For the opinion you can see on the following link a youtube video with a comparable car wash like ours, the washing process is well illustrated there. https://www.clipvault-demo.net/watch?v=Qk7rTzP2mLw Furthermore, we have a bonus card system who has washed our car 10 times gets the 11 laundry for free. From foam additives we use active foam from the comfort care and from the special care gets the vehicle lotus wax, which has the effect that the paint is sealed and keeps the shine longer. We need a design template / print template for our advertising pylon so that the Korvane plates can be printed. The area to be printed is approx. 1.5m wide and approx. 2.70m high. We operate a car wash about 30m long. The washing rollers are equipped with scratch-free Velmo Tex foam material. Before the vehicle is put into the car wash it gets a manual high pressure pre-wash. There are four different washing programs: basic laundry € 7.50 (wheel cleaning, intensive washing, gloss drying comfort care € 10.50 (like base + active foam) special care € 13.00 (like comfort + glossy sealing with lotus wax) premium care € 15.50 (like special care + Underbody wash) The pylon is right on the driveway on a busy road, we want to achieve maximum attention with the pylons. It should not be too much content because the vehicles drive past it, due to an immediate gyro, the speed is however at about 40Km / h. Opening hours Mon-Fri. 08: 00-19: 00 Sat 07: 00-19: 00 The Korvane plates are red. The enclosed files show our pylon with a little appealing design proposal our advertising agency and the real local places. For the opinion you can see on the following link a youtube video with a comparable car wash like ours, the washing process is well illustrated there. https://www.clipvault-demo.net/watch?v=Qk7rTzP2mLw Furthermore, we have a bonus card system who has washed our car 10 times gets the 11 laundry for free. From foam additives we use active foam from the comfort care and from the special care gets the vehicle lotus wax, which has the effect that the paint is sealed and keeps the shine longer. We need a design template / print template for our advertising pylon so that the Korvane plates can be printed. The area to be printed is approx. 1.5m wide and approx. 2.70m high. We operate a car wash about 30m long. The washing rollers are equipped with scratch-free Velmo Tex foam material. Before the vehicle is put into the car wash it gets a manual high pressure pre-wash. There are four different washing programs: basic laundry € 7.50 (wheel cleaning, intensive washing, gloss drying comfort care € 10.50 (like base + active foam) special care € 13.00 (like comfort + glossy sealing with lotus wax) premium care € 15.50 (like special care + Underbody wash) The pylon is right on the driveway on a busy road, we want to achieve maximum attention with the pylons. It should not be too much content because the vehicles drive past it, due to an immediate gyro, the speed is however at about 40Km / h. Opening hours Mon-Fri. 08: 00-19: 00 Sat 07: 00-19: 00 The Korvane plates are red. The enclosed files show our pylon with a little appealing design proposal our advertising agency and the real local places. For the opinion you can see on the following link a youtube video with a comparable car wash like ours, the washing process is well illustrated there. https://www.clipvault-demo.net/watch?v=Qk7rTzP2mLw Furthermore, we have a bonus card system who has washed our car 10 times gets the 11 laundry for free. From foam additives we use active foam from the comfort care and from the special care gets the vehicle lotus wax, which has the effect that the paint is sealed and keeps the shine longer. We need a design template / print template for our advertising pylon so that the Korvane plates can be printed. The area to be printed is approx. 1.5m wide and approx. 2.70m high. We operate a car wash about 30m long. The washing rollers are equipped with scratch-free Velmo Tex foam material. Before the vehicle is put into the car wash it gets a manual high pressure pre-wash. There are four different washing programs: basic laundry € 7.50 (wheel cleaning, intensive washing, gloss drying comfort care € 10.50 (like base + active foam) special care € 13.00 (like comfort + glossy sealing with lotus wax) premium care € 15.50 (like special care + Underbody wash) The pylon is right on the driveway on a busy road, we want to achieve maximum attention with the pylons. It should not be too much content because the vehicles drive past it, due to an immediate gyro, the speed is however at about 40Km / h. Opening hours Mon-Fri. 08: 00-19: 00 Sat 07: 00-19: 00 The Korvane plates are red. The enclosed files show our pylon with a little appealing design proposal our advertising agency and the real local places. For the opinion you can see on the following link a youtube video with a comparable car wash like ours, the washing process is well illustrated there. https://www.clipvault-demo.net/watch?v=Qk7rTzP2mLw Furthermore, we have a bonus card system who has washed our car 10 times gets the 11 laundry for free. From foam additives we use active foam from the comfort care and from the special care gets the vehicle lotus wax, which has the effect that the paint is sealed and keeps the shine longer. We need a design template / print template for our advertising pylon so that the Korvane plates can be printed. The area to be printed is approx. 1.5m wide and approx. 2.70m high. We operate a car wash about 30m long. The washing rollers are equipped with scratch-free Velmo Tex foam material. Before the vehicle is put into the car wash it gets a manual high pressure pre-wash. There are four different washing programs: basic laundry € 7.50 (wheel cleaning, intensive washing, gloss drying comfort care € 10.50 (like base + active foam) special care € 13.00 (like comfort + glossy sealing with lotus wax) premium care € 15.50 (like special care + Underbody wash) The pylon is right on the driveway on a busy road, we want to achieve maximum attention with the pylons. It should not be too much content because the vehicles drive past it, due to an immediate gyro, the speed is however at about 40Km / h. Opening hours Mon-Fri. 08: 00-19: 00 Sat 07: 00-19: 00 The Korvane plates are red. The enclosed files show our pylon with a little appealing design proposal our advertising agency and the real local places. For the opinion you can see on the following link a youtube video with a comparable car wash like ours, the washing process is well illustrated there. https://www.clipvault-demo.net/watch?v=Qk7rTzP2mLw Furthermore, we have a bonus card system who has washed our car 10 times gets the 11 laundry for free. From foam additives we use active foam from the comfort care and from the special care gets the vehicle lotus wax, which has the effect that the paint is sealed and keeps the shine longer. We need a design template / print template for our advertising pylon so that the Korvane plates can be printed. The area to be printed is approx. 1.5m wide and approx. 2.70m high. We operate a car wash about 30m long. The washing rollers are equipped with scratch-free Velmo Tex foam material. Before the vehicle is put into the car wash it gets a manual high pressure pre-wash. There are four different washing programs: basic laundry € 7.50 (wheel cleaning, intensive washing, gloss drying comfort care € 10.50 (like base + active foam) special care € 13.00 (like comfort + glossy sealing with lotus wax) premium care € 15.50 (like special care + Underbody wash) The pylon is right on the driveway on a busy road, we want to achieve maximum attention with the pylons. It should not be too much content because the vehicles drive past it, due to an immediate gyro, the speed is however at about 40Km / h. Opening hours Mon-Fri. 08: 00-19: 00 Sat 07: 00-19: 00 The Korvane plates are red. The enclosed files show our pylon with a little appealing design proposal our advertising agency and the real local places. For the opinion you can see on the following link a youtube video with a comparable car wash like ours, the washing process is well illustrated there. https://www.clipvault-demo.net/watch?v=Qk7rTzP2mLw Furthermore, we have a bonus card system who has washed our car 10 times gets the 11 laundry for free. From foam additives we use active foam from the comfort care and from the special care gets the vehicle lotus wax, which has the effect that the paint is sealed and keeps the shine longer. We need a design template / print template for our advertising pylon so that the Korvane plates can be printed. The area to be printed is approx. 1.5m wide and approx. 2.70m high. We operate a car wash about 30m long. The washing rollers are equipped with scratch-free Velmo Tex foam material. Before the vehicle is put into the car wash it gets a manual high pressure pre-wash. There are four different washing programs: basic laundry € 7.50 (wheel cleaning, intensive washing, gloss drying comfort care € 10.50 (like base + active foam) special care € 13.00 (like comfort + glossy sealing with lotus wax) premium care € 15.50 (like special care + Underbody wash) The pylon is right on the driveway on a busy road, we want to achieve maximum attention with the pylons. It should not be too much content because the vehicles drive past it, due to an immediate gyro, the speed is however at about 40Km / h. Opening hours Mon-Fri. 08: 00-19: 00 Sat 07: 00-19: 00 The Korvane plates are red. The enclosed files show our pylon with a little appealing design proposal our advertising agency and the real local places. For the opinion you can see on the following link a youtube video with a comparable car wash like ours, the washing process is well illustrated there. https://www.clipvault-demo.net/watch?v=Qk7rTzP2mLw Furthermore, we have a bonus card system who has washed our car 10 times gets the 11 laundry for free. From foam additives we use active foam from the comfort care and from the special care gets the vehicle lotus wax, which has the effect that the paint is sealed and keeps the shine longer. We need a design template / print template for our advertising pylon so that the Korvane plates can be printed. The area to be printed is approx. 1.5m wide and approx. 2.70m high. We operate a car wash about 30m long. The washing rollers are equipped with scratch-free Velmo Tex foam material. Before the vehicle is put into the car wash it gets a manual high pressure pre-wash. There are four different washing programs: basic laundry € 7.50 (wheel cleaning, intensive washing, gloss drying comfort care € 10.50 (like base + active foam) special care € 13.00 (like comfort + glossy sealing with lotus wax) premium care € 15.50 (like special care + Underbody wash) The pylon is right on the driveway on a busy road, we want to achieve maximum attention with the pylons. It should not be too much content because the vehicles drive past it, due to an immediate gyro, the speed is however at about 40Km / h. Opening hours Mon-Fri. 08: 00-19: 00 Sat 07: 00-19: 00 The Korvane plates are red. The enclosed files show our pylon with a little appealing design proposal our advertising agency and the real local places. For the opinion you can see on the following link a youtube video with a comparable car wash like ours, the washing process is well illustrated there. https://www.clipvault-demo.net/watch?v=Qk7rTzP2mLw Furthermore, we have a bonus card system who has washed our car 10 times gets the 11 laundry for free. From foam additives we use active foam from the comfort care and from the special care gets the vehicle lotus wax, which has the effect that the paint is sealed and keeps the shine longer. We need a design template / print template for our advertising pylon so that the Korvane plates can be printed. The area to be printed is approx. 1.5m wide and approx. 2.70m high. We operate a car wash about 30m long. The washing rollers are equipped with scratch-free Velmo Tex foam material. Before the vehicle is put into the car wash it gets a manual high pressure pre-wash. There are four different washing programs: basic laundry € 7.50 (wheel cleaning, intensive washing, gloss drying comfort care € 10.50 (like base + active foam) special care € 13.00 (like comfort + glossy sealing with lotus wax) premium care € 15.50 (like special care + Underbody wash) The pylon is right on the driveway on a busy road, we want to achieve maximum attention with the pylons. It should not be too much content because the vehicles drive past it, due to an immediate gyro, the speed is however at about 40Km / h. Opening hours Mon-Fri. 08: 00-19: 00 Sat 07: 00-19: 00 The Korvane plates are red. The enclosed files show our pylon with a little appealing design proposal our advertising agency and the real local places. For the opinion you can see on the following link a youtube video with a comparable car wash like ours, the washing process is well illustrated there. https://www.clipvault-demo.net/watch?v=Qk7rTzP2mLw Furthermore, we have a bonus card system who has washed our car 10 times gets the 11 laundry for free. From foam additives we use active foam from the comfort care and from the special care gets the vehicle lotus wax, which has the effect that the paint is sealed and keeps the shine longer.

Target Market(s)

germany

Colors

Designer to choose colors to be used in the design.

Requirements
Must have
• Print template for the print job in the accepted formats. Of course, the design must be in German
Nice to have
• Colors that attract attention, but are still serious. The content must be perceived when passing by and the customers must be aware of the car wash.
Should not have
• Kitschiges Design Too much content which takes longer to be read.

```html
<!DOCTYPE html>
<html lang="de">
<head>
<meta charset="utf-8">
<title>Autowäsche – Pylon</title>
<link rel="stylesheet" href="https://fonts.googleapis.com/css2?family=Anton&family=Roboto:ital,wght@0,500;0,700;1,700;1,900&display=swap">
<style>
  :root{
    --frame:#000;
    --sky:#7fdcef;
    --sky-deep:#19bfe0;
    --navy:#0b1d50;
    --ocean:#0a5596;
    --glow:#0aa9d6;
    --red:#ef1c25;
    --white:#ffffff;
    --yellow:#ffe81a;
    --cyan-text:#3fd0e6;
    --banner-edge:#0d2d7a;
  }
  *{margin:0;padding:0;box-sizing:border-box}
  html,body{width:960px;height:1200px;overflow:hidden;background:#fff}
  body{position:relative;font-family:"Roboto",Arial,sans-serif}
  .pylon-frame{position:absolute;left:182px;top:98px;width:586px;height:1014px;background:var(--frame)}
  .pylon{position:absolute;left:201px;top:113px;width:548px;height:987px;overflow:hidden;
    background:radial-gradient(ellipse 70% 45% at 55% 52%,var(--glow) 0%,var(--ocean) 55%,var(--navy) 100%)}
  .backdrop{position:absolute;left:0;top:0;width:548px;height:987px}
  .title{position:absolute;left:0;top:66px;width:548px;text-align:center;
    font-family:"Anton",Impact,sans-serif;font-size:90px;line-height:1;letter-spacing:-1px;
    color:var(--white);-webkit-text-stroke:6px var(--banner-edge);paint-order:stroke fill;
    transform:scaleY(1.05)}
  .hero-car{position:absolute;left:277px;top:154px;width:180px;height:122px;border-radius:26px 26px 10px 10px;
    background:linear-gradient(180deg,#2a9be0 0%,#0f62b8 60%,#0a2f6a 100%)}
  .benefits{position:absolute;left:0;top:0;width:548px;list-style:none}
  .benefit{position:absolute;left:82px;color:var(--white);font-weight:700;font-style:italic;font-size:23px;line-height:26px;
    text-shadow:0 2px 2px rgba(0,0,0,.35)}
  .tick{position:absolute;left:-62px;top:-4px;width:48px;height:44px}
  .prices{position:absolute;left:0;top:670px;width:548px}
  .price{position:absolute;width:120px;text-align:center}
  .price-disc{width:80px;height:80px;margin:0 auto;border-radius:50%;background:var(--red);color:var(--white);
    font-weight:700;text-align:center;padding-top:6px}
  .price-disc .cur{display:block;font-size:26px;line-height:26px}
  .price-disc .amount{display:block;font-size:27px;line-height:30px;letter-spacing:-1px}
  .price-name{margin-top:5px;color:var(--white);font-weight:500;font-size:12.5px;line-height:12.5px}
  .promo{position:absolute;left:255px;top:794px;width:251px;height:54px;background:var(--red);
    clip-path:polygon(20px 0,100% 0,100% 100%,0 100%)}
  .promo p{position:absolute;left:30px;top:3px;color:var(--white);font-style:italic;font-weight:700;font-size:23px;line-height:24px}
  .wax-car{position:absolute;left:35px;top:808px;width:162px;height:80px;border-radius:40px 40px 8px 8px;
    background:radial-gradient(ellipse at 50% 60%,rgba(255,255,255,.35),rgba(255,255,255,.05) 70%)}
  .extra{position:absolute;left:206px;top:862px;color:var(--yellow);font-style:italic;font-weight:900;font-size:28px;line-height:30px}
  .wax{position:absolute;left:0;top:892px;width:548px;text-align:center;font-style:italic;font-weight:900;font-size:38px;
    line-height:40px;letter-spacing:-1px;color:#e9ecf2;text-shadow:0 2px 0 #8a93a6}
  .hours-label{position:absolute;left:0;top:940px;width:548px;text-align:center;color:var(--white);font-weight:700;font-size:14px}
  .hours{position:absolute;left:0;top:956px;width:548px;text-align:center;color:var(--cyan-text);font-style:italic;font-weight:700;font-size:19px}
</style>
</head>
<body>
<div class="pylon-frame"></div>
<main class="pylon">
  <svg class="backdrop" viewBox="0 0 548 987" aria-hidden="true">
    <defs>
      <linearGradient id="skyFill" x1="0" y1="0" x2="0" y2="1">
        <stop offset="0" stop-color="#7fdcef"/><stop offset="1" stop-color="#4ccbe7"/>
      </linearGradient>
    </defs>
    <path d="M0,0 H548 V338 C470,350 390,335 300,300 C200,262 100,240 0,253 Z" fill="url(#skyFill)"/>
    <path d="M0,190 C120,180 220,215 310,258 C390,296 470,318 548,282 V302 C470,336 390,318 300,278 C210,238 110,215 0,226 Z" fill="#fff"/>
    <path d="M0,232 C110,220 210,246 300,286 C390,326 470,346 548,322 V338 C470,354 390,336 300,300 C200,262 100,240 0,253 Z" fill="#fff"/>
    <path d="M380,340 C440,355 500,350 548,338 V345 C500,360 440,362 380,340 Z" fill="#000"/>
    <path d="M16,70 L140,56 C185,22 240,8 280,8 C325,8 370,22 405,46 L538,64 L518,168 L497,172 L495,181 L130,196 L128,178 L46,172 Z"
      fill="var(--red)" stroke="var(--banner-edge)" stroke-width="5" stroke-linejoin="round"/>
  </svg>

  <h1 class="title">AUTOWÄSCHE</h1>
  <div class="hero-car" role="img" aria-label="Illustration: blaues Auto von vorn in Schaum und Seifenblasen"></div>

  <ul class="benefits">
    <li class="benefit" style="top:328px">
      <svg class="tick" viewBox="0 0 48 44" aria-hidden="true"><circle cx="20" cy="24" r="20" fill="var(--red)"/><path d="M9,24 L18,33 L46,6 L18,27 Z" fill="#fff"/></svg>
      Unsere verschiedenen<br>Waschprogramme<br>garantieren Ihnen echte Qualität und
    </li>
    <li class="benefit" style="top:426px">
      <svg class="tick" viewBox="0 0 48 44" aria-hidden="true"><circle cx="20" cy="24" r="20" fill="var(--red)"/><path d="M9,24 L18,33 L46,6 L18,27 Z" fill="#fff"/></svg>
      Alle unsere Waschprogramme<br>nutzen Aktiv-Schaum
    </li>
    <li class="benefit" style="top:495px;line-height:28px">
      <svg class="tick" viewBox="0 0 48 44" aria-hidden="true"><circle cx="20" cy="24" r="20" fill="var(--red)"/><path d="M9,24 L18,33 L46,6 L18,27 Z" fill="#fff"/></svg>
      Neuwertiger Waschtechnik zu<br>glänzenden Ergebnissen
    </li>
    <li class="benefit" style="top:567px;left:78px;line-height:27px">
      <svg class="tick" viewBox="0 0 48 44" aria-hidden="true" style="left:-58px"><circle cx="20" cy="24" r="20" fill="var(--red)"/><path d="M9,24 L18,33 L46,6 L18,27 Z" fill="#fff"/></svg>
      Und nutzen Sie unsere Bonuskarte.<br>Nach 10 Wäschen erhalten<br>1 Wäsche kostenlos&nbsp; nach&nbsp; Wahl
    </li>
  </ul>

  <section class="prices">
    <div class="price" style="left:32px"><div class="price-disc"><span class="cur">€</span><span class="amount">7.50</span></div><p class="price-name">GRUNDLEGENDE<br>WÄSCHE</p></div>
    <div class="price" style="left:152px"><div class="price-disc"><span class="cur">€</span><span class="amount">10.50</span></div><p class="price-name">KOMFORT<br>PFLEGE</p></div>
    <div class="price" style="left:268px"><div class="price-disc"><span class="cur">€</span><span class="amount">13.00</span></div><p class="price-name">BESONDERE<br>PFLEGE</p></div>
    <div class="price" style="left:382px"><div class="price-disc"><span class="cur">€</span><span class="amount">15.50</span></div><p class="price-name">PREMIUM<br>PFLEGE</p></div>
  </section>

  <div class="promo"><p>Perfekte Wäsche<br>auch für 1hr Auto</p></div>
  <div class="wax-car" role="img" aria-label="Illustration: Sportwagen-Umriss mit Glanzsternen"></div>
  <p class="extra">ETWAS BESONDERES</p>
  <p class="wax">ZUSÄTZLICH LOTUSWACHS</p>
  <p class="hours-label">ÖFFNUNGSZEITEN</p>
  <p class="hours">Mo-Frei. 08:00-19:00 Uhr,&nbsp; Sa 07:00-19:00 Uhr</p>
</main>
</body>
</html>
```